Calden L - Premium Business Cards

Background of Calden L
Calden Leafworks is a cigar mobile lounge where guests become family. A place of luxury, relaxation, and ambiance is the global popularity demand. Calden Leafworks strives to provide first-class service of quality and products. Our goal is to ensure that every guest is treated and serviced as a VIP.

Calden Leafworks was founded by Dennis Markow Jr in January 2020. After 15 years of cigar reviews and research Dennis decided it was time to launch his own cigar brand and boutique cigar company. With a wealth of knowledge and years of experience Calden Leafworks was born. With opulence for all cultures, Calden Leafworks offers hand rolled cigars with premium blend tobacco from sweet to bold imported from Costa Rica, Dominican Republic, and Nicaragua. Thank you for your business!

Objective:
Create a business card template to be used for all employees. Design should communicate premium and classy. And should use earth tone colors.

Design should include:
1. Client wants to incorporate the cigar leaf
2. Logo
3. Tagline: Savor every draw
3. Content info:
Kevin Oldacre
Owner
555-017-4863
koldacre@caldenleaf.com
caldenleafworks.com

```html
<!DOCTYPE html>
<html lang="en">
<head>
<meta charset="utf-8">
<title>Calden Leafworks – Business Cards</title>
<link rel="stylesheet" href="https://fonts.googleapis.com/css2?family=Montserrat:wght@500;600;700&display=swap">
<style>
  :root {
    --ink: #231f20;
    --paper: #ffffff;
    --stage: #e9e6e2;
    --muted: #3a3637;
  }
  * { box-sizing: border-box; margin: 0; padding: 0; }
  html, body { width: 1200px; height: 900px; overflow: hidden; }
  body {
    background: var(--stage);
    font-family: "Montserrat", Arial, sans-serif;
    display: flex;
    flex-direction: column;
    align-items: center;
    justify-content: space-evenly;
  }
  .card {
    position: relative;
    width: 700px;
    height: 400px;
    overflow: hidden;
    box-shadow: 0 6px 18px rgba(0,0,0,.18);
  }
  .card--front {
    background: var(--ink);
    display: flex;
    align-items: center;
    justify-content: center;
  }
  .brand-name {
    font-weight: 700;
    letter-spacing: .5px;
    white-space: nowrap;
  }
  .card--front .brand-name { color: var(--paper); font-size: 50px; }

  .card--back { background: var(--paper); color: var(--ink); }
  .card--back .brand-name {
    position: absolute; top: 60px; right: 48px;
    font-size: 32px; color: var(--ink);
  }
  .holder { position: absolute; top: 70px; left: 52px; }
  .holder-name { font-size: 26px; font-weight: 700; text-transform: uppercase; line-height: 1.1; }
  .holder-role { font-size: 17px; font-weight: 500; color: var(--muted); }

  .contact { position: absolute; left: 52px; top: 190px; list-style: none; }
  .contact li {
    display: flex; align-items: center; gap: 10px;
    font-size: 17px; font-weight: 500; line-height: 28px;
  }
  .contact svg { width: 17px; height: 17px; flex: none; }
  .icon-solid { fill: var(--ink); }
  .icon-line { fill: none; stroke: var(--ink); stroke-width: 1.8; }

  .wave { position: absolute; inset: 0; width: 100%; height: 100%; }
  .tagline {
    position: absolute; right: 44px; bottom: 96px;
    color: var(--paper); font-size: 19px; font-weight: 600;
    letter-spacing: 1px; text-transform: uppercase;
    transform: rotate(-14deg); transform-origin: right bottom;
    white-space: nowrap;
  }
</style>
</head>
<body>
  <section class="card card--front">
    <span class="brand-name">Calden Leafworks</span>
  </section>

  <section class="card card--back">
    <svg class="wave" viewBox="0 0 700 400" preserveAspectRatio="none" aria-hidden="true">
      <path d="M0 315 C 220 318, 330 290, 460 220 S 640 125, 700 120 L700 400 L0 400 Z" fill="var(--ink)"/>
      <path d="M0 335 C 190 332, 300 300, 420 225" stroke="var(--paper)" stroke-width="3" fill="none"/>
    </svg>

    <span class="brand-name">Calden Leafworks</span>

    <div class="holder">
      <p class="holder-name">Kevin Oldacre</p>
      <p class="holder-role">Owner</p>
    </div>

    <ul class="contact">
      <li>
        <svg class="icon-solid" viewBox="0 0 24 24"><path d="M6.6 10.8a15.1 15.1 0 0 0 6.6 6.6l2.2-2.2a1 1 0 0 1 1-.25 11.4 11.4 0 0 0 3.6.57 1 1 0 0 1 1 1V20a1 1 0 0 1-1 1A17 17 0 0 1 3 4a1 1 0 0 1 1-1h3.5a1 1 0 0 1 1 1c0 1.25.2 2.45.57 3.57a1 1 0 0 1-.25 1z"/></svg>
        555-017-4863
      </li>
      <li>
        <svg class="icon-line" viewBox="0 0 24 24"><path d="M2 5h20v14H2z M2 5l10 8 10-8"/></svg>
        koldacre@caldenleaf.com
      </li>
      <li>
        <svg class="icon-line" viewBox="0 0 24 24"><circle cx="12" cy="12" r="9.5"/><ellipse cx="12" cy="12" rx="4.5" ry="9.5"/><path d="M2.5 12h19M4 7h16M4 17h16"/></svg>
        caldenleafworks.com
      </li>
    </ul>

    <p class="tagline">Savor Every Draw</p>
  </section>
</body>
</html>
```